Business Cards for new orthopaedic surgery practice

My husband and I are starting our own orthopaedic surgery practice. We are looking for a business card that is uniform, but one will have my name/title and the other will have his. You can just create one design with my name on it for now. But when I choose your design as the winning design I will ask that you add another copy with his name/title.

We are looking for classy, simple, elite all in one. We like dark blues/a little gold/yellow. Something that goes with our logo. We want our logo incorporated. Here is all the info you need:
Business name: RV Bone & Vitality Center
Location: 38517 North Willowmere Ave
Maple Hollow, FL 34286
Phone: 954-218-4063
Fax: 954-582-7341
Email: info@myrvbonecare.example

Names: Lydia Vance, M.D.
Board Certified Hand and Upper Extremity Surgeon

Ebo Dansu, M.D.
Board Certified Hip & Knee Replacement/General Orthopaedic Surgeon

Can decide what you want to put on the back. Maybe a slogan:
Grounded in Care. Centered on You

I am just going to upload our logo. The only thing is if we select you as the winning design, the location, and phone numbers may change. We will need your help to update that once fully solidified.

Industry/Entity Type

Medical

Contact Information for Business Card

Colors
0054AA
0677BA
7BADD7
CADEEF
E8F1F8
0094D4
00A9DD
6FCCEA
C7EBF8
E9F6FB

Requirements
Must have
• class, appeal,
Should not have
• We want to air on the side of masculine if we are looking at masculine vs. feminine feel. But we still want it classy, sophisticated, and something we will love

```html
<!DOCTYPE html>
<html lang="en">
<head>
<meta charset="utf-8">
<title>RV Bone &amp; Vitality Center – Business Card</title>
<link rel="stylesheet" href="https://fonts.googleapis.com/css2?family=Cormorant+Garamond:wght@700&family=Arimo:wght@400&display=swap">
<style>
  :root {
    --page: #e4e4e2;
    --paper: #fbfbfa;
    --navy: #1f2f5c;
    --navy-top: #263861;
    --navy-bottom: #1c2953;
    --gold: #c8a05a;
    --ink: #4a4a4a;
    --rule: #cdbf9e;
  }
  * { margin: 0; padding: 0; box-sizing: border-box; }
  html, body { width: 1200px; height: 1200px; overflow: hidden; }
  body { background: var(--page); position: relative; font-family: "Arimo", Arial, sans-serif; }

  .card {
    position: absolute;
    width: 688px;
    height: 393px;
  }
  .card--front { left: 267px; top: 159px; background: var(--paper); }
  .card--back {
    left: 262px; top: 653px;
    background: linear-gradient(180deg, var(--navy-top), var(--navy-bottom));
  }

  .brand {
    position: absolute;
    width: 196px; height: 196px;
    border: 2px solid var(--gold);
    border-radius: 50%;
    display: flex; align-items: center; justify-content: center;
    text-align: center;
    font-family: "Cormorant Garamond", Georgia, serif;
    font-weight: 700;
    font-size: 23px;
    line-height: 1.15;
    letter-spacing: 1.5px;
    text-transform: uppercase;
    color: var(--navy);
  }
  .card--front .brand { left: 92px; top: 90px; }
  .card--back .brand { left: 244px; top: 93px; color: #ffffff; }

  .divider {
    position: absolute; left: 320px; top: 94px;
    width: 1px; height: 197px; background: var(--rule);
  }

  .details { position: absolute; left: 345px; top: 84px; }
  .details__name {
    font-family: "Cormorant Garamond", Georgia, serif;
    font-weight: 700; font-size: 25px; letter-spacing: 0.6px;
    color: var(--navy); line-height: 1;
  }
  .details__title {
    margin-top: 7px; color: var(--gold);
    font-size: 15px; line-height: 19px;
  }
  .details__address {
    margin-top: 11px; color: var(--ink);
    font-size: 16px; line-height: 21px;
  }
  .contact-list { list-style: none; margin-top: 12px; }
  .contact-list li {
    display: flex; align-items: center;
    height: 20.5px; color: var(--ink); font-size: 16px;
  }
  .contact-list svg { width: 13px; height: 13px; margin-right: 12px; fill: var(--gold); flex: none; }

  .slogan {
    position: absolute; left: 0; right: 0; top: 335px;
    text-align: center; color: var(--gold);
    font-size: 15.5px; letter-spacing: 3px; text-transform: uppercase;
  }
</style>
</head>
<body>

<section class="card card--front" aria-label="Business card front">
  <div class="brand">RV Bone &amp;<br>Vitality<br>Center</div>
  <div class="divider"></div>
  <div class="details">
    <h1 class="details__name">LYDIA VANCE, M.D.</h1>
    <p class="details__title">Board Certified Hand and<br>Upper Extremity Surgeon</p>
    <p class="details__address">38517 North Willowmere Ave<br>Maple Hollow, FL 34286</p>
    <ul class="contact-list">
      <li><svg viewBox="0 0 16 16" aria-hidden="true"><path d="M3.6 1l2.6 3-1.4 1.8c.9 2 2.5 3.6 4.4 4.5l1.8-1.4 3 2.6-1.5 2.5C7 13.5 2.5 9 1 3.1z"/></svg>954-218-4063</li>
      <li><svg viewBox="0 0 16 16" aria-hidden="true"><path d="M4 1h8v4H4zM1 6h14v6h-2v-2H3v2H1zM4 11h8v4H4z"/></svg>954-582-7341</li>
      <li><svg viewBox="0 0 16 16" aria-hidden="true"><path d="M1 3h14v1.5L8 9 1 4.5zM1 6.3l7 4.5 7-4.5V13H1z"/></svg>info@myrvbonecare.example</li>
      <li><svg viewBox="0 0 16 16" aria-hidden="true"><path d="M8 1a7 7 0 100 14A7 7 0 008 1zm-.5 2.2c-.6.7-1.8.9-1.5 2 .3 1 1.8.6 2 1.8.2 1-1 1.3-.7 2.6.2.9 1 1.6.6 2.6A5 5 0 013.2 6.3c.9.4 1.6.1 1.8-.8.3-1.2 1.2-1.9 2.5-2.3zm3.3 1c.4.9-.4 1.4.2 2.3.6.8 1.9.4 2 1.5a5 5 0 01-1.4 3.6c-.5-1-.2-2-1.2-2.6-.8-.5-1.6-1.4-1-2.3.4-.7 1.3-1.1 1.4-2.5z"/></svg>www.myrvbonecare.example</li>
    </ul>
  </div>
</section>

<section class="card card--back" aria-label="Business card back">
  <div class="brand">RV Bone &amp;<br>Vitality<br>Center</div>
  <p class="slogan">Grounded in Care. Centered on You</p>
</section>

</body>
</html>
```